Orvane Thinner Logo and Packaging Design

We are seeking a striking and professional logo and packaging design for our new product line, Orvane Thinner. This logo will be used on the packaging for three different sizes of half-transparent carboys: 1L, 4L, and 20L. Orvane Thinner is a high-quality solvent brand known for its excellent solvency, fast-drying properties, and pleasant smell. The logo should feature an eagle motif to symbolize power and precision, and our slogan, "FLY WITH QUALITY." The design should be suitable for placement on hardware store and warehouse shelves. Additionally, we need the designer to create an eagle logo to accompany the packaging.

Packaging Dimensions:
1L Carboy:
Front: 71mm height x 142mm width
Side: 71mm height x 73mm width
4L Carboy:
Front: 160mm height x 170mm width
Side: 160mm height x 120mm width
20L Carboy:
Front: 245mm height x 190mm width
Side: 215mm height x 190mm width
Front Label Requirements:

Product Name: Thinner QXR
Volume: 20L
Precautionary Statements:
Keep Away from Sources of ignition - No Smoking
Avoid Contact with Eyes
Do Not Empty into Drains or Sewers
Take Precautionary Measures Against Static Discharge
Hazard Statements:
Flammable Liquid and Vapor
May be fatal if swallowed or enters Airways
Causes Skin Irritation
Causes Serious Eye Irritation
Causes Damage to Organs if Prolonged or Repeated Exposure
Hazard Pictograms: (Include relevant hazard symbols)
Design Requirements:

Logo: Eagle motif (to be designed by the designer)
Slogan: FLY WITH QUALITY
Color Scheme: Designer to recommend (should be striking and professional for retail display)

Please see my latest picture. Kindly note the packaging is in Plastic Carboy (not in metal tin as per PS).

Eagle to be more majestic and bigger (as if soaring in the sky).
Singapore landscape as background to have Singapore identity such as KTR, Corvale wheel, terrace at the cove etc.

Eagle to be more majestic and bigger, wings to spread wide.
We not want it to be of photo style, but more on a cartoon style. Please see my latest file uploaded.

Target Market(s)

Our target market includes painting companies, construction companies, direct household consumers, and industrial users who require high-quality solvents for various applications.

Industry/Entity Type

Chemical, spray paint and painting, household, industrial

Requirements
Must have
• Professional and Striking Design: Eye-catching and professional packaging for retail shelves. Eagle Logo: A strong, precise eagle logo. Slogan: "FLY WITH QUALITY" prominently displayed. Clear Precautionary and Hazard Statements: Important safety information and pictograms. Volume Indication: Clearly marked (e.g., 1L, 4L, 20L). Eagle to be more majestic and bigger (as if soaring in the sky). Singapore landscape as background to have Singapore identity such as KTR, Corvale wheel, terrace at the cove etc.
Nice to have
• Color Scheme Recommendations: Suggestions for a professional, striking color scheme. Versatility: Design elements adaptable across different sizes of packaging. Environmentally Friendly Elements: Indications of sustainability or eco-friendliness in the design.
Should not have
• Overly Complex Designs: Avoid cluttered or overly intricate designs that detract from readability. Inconsistent Branding: Ensure all elements are cohesive and align with the brand identity.

```html
<!DOCTYPE html>
<html lang="en">
<head>
<meta charset="utf-8">
<title>Orvane Thinner – 20L Label</title>
<link href="https://fonts.googleapis.com/css2?family=Montserrat:wght@400;600;700&display=swap" rel="stylesheet">
<style>
  :root{
    --bg:#e8e8e9;
    --label:#f3f3f3;
    --orange:#e05a36;
    --ink:#333333;
    --white:#ffffff;
    --warn-yellow:#f2c200;
  }
  *{box-sizing:border-box;margin:0;padding:0}
  html,body{width:1200px;height:722px;overflow:hidden}
  body{background:var(--bg);font-family:"Montserrat",sans-serif;color:var(--ink);position:relative}

  .label{position:absolute;top:81px;height:560px;background:var(--label);box-shadow:0 2px 10px rgba(0,0,0,.08)}
  .label--side{left:215px;width:300px}
  .label--front{left:545px;width:440px}

  .product-heading{position:absolute;top:34px;left:0;right:0;display:flex;align-items:center;gap:12px}
  .product-heading__bar{height:10px;background:var(--orange);flex:1}
  .product-heading__text{font-weight:700;white-space:nowrap}
  .label--front .product-heading__text{font-size:26px;letter-spacing:.5px}
  .label--side .product-heading__text{font-size:16px}
  .label--side .product-heading__bar:last-child{flex:0 0 0}

  .brand-mark{position:absolute;left:50%;transform:translateX(-50%);border-radius:50%;background:var(--orange)}
  .label--front .brand-mark{top:92px;width:58px;height:58px}
  .label--side .brand-mark{top:86px;width:46px;height:46px}

  .brand-name{position:absolute;left:0;right:0;text-align:center;font-weight:600;letter-spacing:1px;color:var(--ink)}
  .label--side .brand-name{top:156px;font-size:16px}

  .band{position:absolute;left:0;right:0;top:205px;height:185px;background:var(--orange)}
  .brand-tab{position:absolute;top:0;left:50%;transform:translateX(-50%);width:310px;height:58px;background:var(--label);border-radius:0 0 26px 26px;display:flex;align-items:center;justify-content:center;font-weight:600;font-size:22px;letter-spacing:1.5px}

  .slogan{position:absolute;left:50%;transform:translateX(-50%);border:2px solid rgba(255,255,255,.8);border-radius:10px;color:var(--white);font-weight:600;display:flex;align-items:center;justify-content:center;text-align:center;letter-spacing:1px}
  .label--front .slogan{top:90px;width:330px;height:64px;font-size:20px}
  .label--side .slogan{top:38px;width:190px;height:110px;font-size:21px;line-height:1.2}

  .safety{position:absolute;left:28px;top:428px;width:250px;font-size:7px;line-height:1.45}
  .safety__title{font-weight:700;font-size:7.5px;margin-top:6px}
  .safety__title:first-child{margin-top:0}
  .safety ul{list-style:none}
  .safety li::before{content:"• "}

  .volume{position:absolute;font-weight:700}
  .label--front .volume{right:32px;bottom:40px;font-size:58px}
  .label--side .volume{left:40px;bottom:40px;font-size:30px}

  .pictograms{position:absolute;left:20px;top:420px;display:flex;gap:8px}
  .pictogram{width:34px;height:31px}
</style>
</head>
<body>

<section class="label label--side" aria-label="Side label">
  <div class="product-heading">
    <span class="product-heading__bar"></span>
    <span class="product-heading__text">THINNER QXR</span>
    <span class="product-heading__bar"></span>
  </div>
  <span class="brand-mark" aria-hidden="true"></span>
  <p class="brand-name">ORVANE THINNER</p>
  <div class="band">
    <p class="slogan">FLY WITH<br>QUALITY</p>
  </div>
  <div class="pictograms">
    <svg class="pictogram" viewBox="0 0 34 31" role="img" aria-label="Flammable hazard pictogram"><polygon points="17,2 32,29 2,29" fill="var(--warn-yellow)" stroke="#222" stroke-width="2"/></svg>
    <svg class="pictogram" viewBox="0 0 34 31" role="img" aria-label="Acute toxicity hazard pictogram"><polygon points="17,2 32,29 2,29" fill="var(--warn-yellow)" stroke="#222" stroke-width="2"/></svg>
    <svg class="pictogram" viewBox="0 0 34 31" role="img" aria-label="Health hazard pictogram"><polygon points="17,2 32,29 2,29" fill="var(--warn-yellow)" stroke="#222" stroke-width="2"/></svg>
  </div>
  <p class="volume">20L</p>
</section>

<section class="label label--front" aria-label="Front label">
  <div class="product-heading">
    <span class="product-heading__bar"></span>
    <span class="product-heading__text">THINNER QXR</span>
    <span class="product-heading__bar"></span>
  </div>
  <span class="brand-mark" aria-hidden="true"></span>
  <div class="band">
    <p class="brand-tab">ORVANE THINNER</p>
    <p class="slogan">FLY WITH QUALITY</p>
  </div>
  <div class="safety">
    <p class="safety__title">Precautionary</p>
    <ul>
      <li>Keep Away from Sources of Ignition - No Smoking</li>
      <li>Avoid Contact with Eyes</li>
      <li>Do Not Empty into Drains or Sewers</li>
      <li>Take Precautionary Measures Against Static Discharge</li>
    </ul>
    <p class="safety__title">Hazard</p>
    <ul>
      <li>Flammable Liquid and Vapor</li>
      <li>May be fatal if swallowed or enters Airways</li>
      <li>Causes Skin Irritation</li>
      <li>Causes Serious Eye Irritation</li>
      <li>Causes Damage to Organs if Prolonged or Repeated Exposure</li>
    </ul>
  </div>
  <p class="volume">20L</p>
</section>

</body>
</html>
```